Spy/Espionage/Counterintelligence Membership Community Needs a PowerPoint Template

We need a powerpoint template for one of our business verticals focused on spies, espionage, and counterintelligence. The name of it is "Brass Lantern Guild" and the logo is attached. Brass Lantern Guild is a community that connects people with experts in espionage and counterintelligence through an online social network, as well as in-person events. We would like to see designs that incorporate the red and black of the logo. The design should communicate mystery/suspense and peak curiosity.

Target Market(s)

Late 20s to baby boomers, male

Industry/Entity Type

Social Club

Font styles to use
Sans Serif

Colors
ec1f27
000000
ffffff

Requirements
Must have
• A user-friendly ppt template file. Incorporate basic fonts that don't have to be installed on every computer for presentations. A cover slide and a basic inside slide. A white background. I will also need graphic source files.
Nice to have
• Plenty of space for slide title and body content. Logo on every slide.
Should not have
• Inconsistency with fonts. Misalignment of images.

```html
<!DOCTYPE html>
<html lang="en">
<head>
<meta charset="utf-8">
<title>Project Title Here</title>
<link rel="stylesheet" href="https://fonts.googleapis.com/css2?family=Questrial&family=Roboto:wght@400;700&display=swap">
<style>
  :root {
    --brand-red: #c8000a;
    --deep-red: #b01e28;
    --slate: #606060;
    --ink: #111111;
    --text: #3a3a3a;
    --panel: #f2f3f5;
    --ring: #d4d4d4;
    --rule: #c9c9c9;
    --footer: #1a1a1a;
    --white: #ffffff;
  }
  * { box-sizing: border-box; margin: 0; padding: 0; }
  html, body { width: 1200px; height: 900px; overflow: hidden; background: var(--white); }
  .slide { position: relative; width: 1200px; height: 900px; background: var(--white); font-family: "Roboto", Arial, sans-serif; }

  .slide-header { position: absolute; left: 0; top: 0; width: 1200px; height: 75px; background: var(--brand-red); border-bottom: 3px solid var(--white); box-shadow: 0 4px 0 -1px var(--ink); }
  .slide-title { position: absolute; left: 20px; top: 12px; font-family: "Questrial", Arial, sans-serif; font-size: 45px; color: var(--white); font-weight: 400; }
  .brand { position: absolute; right: 12px; top: 17px; display: flex; align-items: center; gap: 8px; }
  .brand-dot { width: 36px; height: 36px; border-radius: 50%; background: var(--ink); }
  .brand-name { font-family: "Questrial", Arial, sans-serif; font-size: 30px; color: var(--ink); }

  .intro-heading { position: absolute; left: 51px; top: 125px; font-size: 23px; font-weight: 700; color: var(--ink); }
  .intro-body { position: absolute; left: 52px; top: 176px; font-size: 17.5px; line-height: 30px; color: var(--text); }

  .timeline-line { position: absolute; left: 220px; top: 353px; width: 756px; height: 4px; background: var(--rule); }
  .year { position: absolute; top: 301px; width: 108px; height: 108px; margin-left: -54px; border-radius: 50%; background: var(--white); border: 3px solid var(--ring); display: flex; align-items: center; justify-content: center; }
  .year span { width: 94px; height: 94px; border-radius: 50%; display: flex; align-items: center; justify-content: center; font-size: 30px; font-weight: 700; color: var(--white); }

  .card { position: absolute; top: 414px; width: 333px; height: 398px; background: var(--panel); border: 1.5px solid var(--brand-red); border-radius: 4px; }
  .card-head { position: relative; height: 63px; display: flex; align-items: center; justify-content: center; color: var(--white); font-size: 22px; font-weight: 700; letter-spacing: 0.5px; border-radius: 3px 3px 0 0; }
  .card-head::before { content: ""; position: absolute; left: 50%; top: -12px; margin-left: -13px; border-left: 13px solid transparent; border-right: 13px solid transparent; border-bottom: 13px solid currentColor; }
  .card-body { padding: 24px 30px 0 36px; font-size: 17.5px; line-height: 30px; color: var(--text); }

  .card--first { left: 56px; }
  .card--first .card-head, .card--first .year-fill { background: var(--brand-red); }
  .card--second { left: 432px; border-color: var(--deep-red); }
  .card--third { left: 813px; height: 395px; border-color: var(--slate); }

  .slide-footer { position: absolute; left: 0; top: 856px; width: 1200px; height: 44px; background: var(--footer); }
  .copyright { position: absolute; left: 11px; top: 10px; font-family: "Questrial", Arial, sans-serif; font-size: 20px; color: var(--white); }
  .page-number { position: absolute; right: 6px; top: 5px; width: 34px; height: 34px; border-radius: 50%; background: var(--brand-red); border: 2px solid var(--white); color: var(--white); font-family: "Questrial", Arial, sans-serif; font-size: 19px; display: flex; align-items: center; justify-content: center; }
</style>
</head>
<body>
<main class="slide">
  <header class="slide-header">
    <h1 class="slide-title">Project Title Here</h1>
    <div class="brand"><span class="brand-dot"></span><span class="brand-name">Brass Lantern Guild</span></div>
  </header>

  <h2 class="intro-heading">Lorem ipsum dolor sit Lorem ipsum dolor sit&nbsp; Lorem ipsum dolor sit</h2>
  <p class="intro-body">Lorem ipsum dolor sit Lorem ipsum dolor sit&nbsp; Lorem ipsum dolor sit Lorem ipsum dolor sit&nbsp; Lorem ipsum dolor sit Lorem ipsum<br>dolor sit&nbsp; Lorem ipsum dolor sit Lorem ipsum dolor sit&nbsp; Lorem ipsum dolor sit Lorem ipsum dolor sit&nbsp; Lorem ipsum dolor sit Lorem<br>ipsum dolor sit&nbsp; Lorem ipsum dolor sit Lorem ipsum dolor sit&nbsp; Lorem ipsum dolor sit Lorem ipsum dolor sit</p>

  <div class="timeline-line"></div>
  <div class="year" style="left:220px"><span style="background:var(--brand-red)">1995</span></div>
  <div class="year" style="left:595px"><span style="background:var(--deep-red)">2005</span></div>
  <div class="year" style="left:976px"><span style="background:var(--slate)">2015</span></div>

  <section class="card card--first">
    <h3 class="card-head" style="background:var(--brand-red);color:var(--white)"><span style="position:relative">TITLE HERE</span></h3>
    <p class="card-body">Lorem ipsum dolor sit Lorem<br>ipsum dolor sit&nbsp; Lorem ipsum<br>dolor sit Lorem ipsum dolor sit<br>Lorem ipsum dolor sit Lorem<br>ipsum dolor sit&nbsp; Lorem ipsum<br>dolor sit Lorem ipsum dolor sit<br>Lorem ipsum dolor sit Lorem<br>ipsum dolor sit&nbsp; Lorem ipsum<br>dolor sit</p>
  </section>
  <section class="card card--second">
    <h3 class="card-head" style="background:var(--deep-red);color:var(--deep-red)"><span style="color:var(--white)">TITLE HERE</span></h3>
    <p class="card-body">Lorem ipsum dolor sit Lorem<br>ipsum dolor sit&nbsp; Lorem ipsum<br>dolor sit Lorem ipsum dolor sit<br>Lorem ipsum dolor sit Lorem<br>ipsum dolor sit&nbsp; Lorem ipsum<br>dolor sit Lorem ipsum dolor sit<br>Lorem ipsum dolor sit Lorem<br>ipsum dolor sit&nbsp; Lorem ipsum<br>dolor sit</p>
  </section>
  <section class="card card--third">
    <h3 class="card-head" style="background:var(--slate);color:var(--slate)"><span style="color:var(--white)">TITLE HERE</span></h3>
    <p class="card-body">Lorem ipsum dolor sit Lorem<br>ipsum dolor sit&nbsp; Lorem ipsum<br>dolor sit Lorem ipsum dolor sit<br>Lorem ipsum dolor sit Lorem<br>ipsum dolor sit&nbsp; Lorem ipsum<br>dolor sit Lorem ipsum dolor sit<br>Lorem ipsum dolor sit Lorem<br>ipsum dolor sit&nbsp; Lorem ipsum<br>dolor sit</p>
  </section>

  <footer class="slide-footer">
    <span class="copyright">Copyright text here</span>
    <span class="page-number">1</span>
  </footer>
</main>
</body>
</html>
```